Roofing Contractor business card redesign

I want to redesign my business card with a fresh, eye catching concept

Target Market(s)

Residential Roofing Clients, potential employees, and subcontractors.

Industry/Entity Type

Business

Colors

Designer to choose colors to be used in the design.

Requirements
Nice to have
• I just want something that's more pleasing to the eye. You can use a combination of either / or of my logos.

```html
<!DOCTYPE html>
<html lang="en">
<head>
<meta charset="utf-8">
<title>Ridgeline Builders – Business Card</title>
<link rel="stylesheet" href="https://fonts.googleapis.com/css2?family=Oswald:wght@500&family=Open+Sans:wght@400;700&display=swap">
<style>
  :root {
    --page-bg: #e9e6e3;
    --maroon: #43110d;
    --orange: #e77325;
    --text-light: #f4ece8;
    --disc-light: #ffffff;
    --disc-shade: #cfcfd1;
    --brand: #4a1410;
  }
  html, body {
    margin: 0;
    width: 1200px;
    height: 900px;
    overflow: hidden;
    background: var(--page-bg);
  }
  .card {
    position: absolute;
    left: 120px;
    top: 154px;
    width: 960px;
    height: 592px;
    background: var(--maroon);
    overflow: hidden;
    box-shadow: 0 10px 30px rgba(0,0,0,0.18);
    font-family: "Open Sans", Arial, sans-serif;
    color: var(--text-light);
  }
  .card__accent {
    position: absolute;
    left: 646px;
    top: 0;
    right: 0;
    bottom: 0;
    background: var(--orange);
  }
  .card__disc {
    position: absolute;
    left: 388px;
    top: 38px;
    width: 516px;
    height: 516px;
    border-radius: 50%;
    background: radial-gradient(circle at 45% 40%, var(--disc-light) 0%, #f1f1f2 45%, var(--disc-shade) 100%);
    display: flex;
    flex-direction: column;
    align-items: center;
    justify-content: center;
  }
  .brand__dot {
    width: 34px;
    height: 34px;
    border-radius: 50%;
    background: var(--brand);
    margin-bottom: 16px;
  }
  .brand__name {
    font-family: "Open Sans", Arial, sans-serif;
    font-weight: 700;
    font-size: 44px;
    line-height: 1.15;
    color: var(--brand);
    text-align: center;
    margin: 0;
  }
  .person {
    position: absolute;
    left: 56px;
    top: 60px;
  }
  .person__name {
    font-family: "Oswald", "Arial Narrow", sans-serif;
    font-weight: 500;
    font-size: 44px;
    line-height: 1;
    margin: 0 0 12px;
  }
  .person__title {
    font-size: 25px;
    line-height: 36px;
    margin: 0;
  }
  .contact {
    position: absolute;
    left: 56px;
    top: 292px;
    list-style: none;
    margin: 0;
    padding: 0;
    font-size: 24px;
    line-height: 34.5px;
  }
  .contact__item {
    display: flex;
    align-items: center;
    gap: 10px;
  }
  .contact__icon {
    width: 20px;
    height: 20px;
    fill: var(--text-light);
    flex: none;
  }
  .address {
    position: absolute;
    left: 56px;
    top: 456px;
    font-size: 24px;
    line-height: 35px;
    font-style: normal;
  }
</style>
</head>
<body>
  <div class="card">
    <div class="card__accent"></div>

    <div class="card__disc">
      <div class="brand__dot"></div>
      <p class="brand__name">Ridgeline<br>Builders, Inc.</p>
    </div>

    <div class="person">
      <h1 class="person__name">Mark Holloway</h1>
      <p class="person__title">Summit certified Roof Inspector<br>Licensed Property Adjuster</p>
    </div>

    <ul class="contact">
      <li class="contact__item">
        <svg class="contact__icon" viewBox="0 0 20 20"><path d="M2 7c0-3 3-4 8-4s8 1 8 4l-3 1-1-2H6L5 8 2 7zM4 9h12l1 8H3l1-8zm6 2a2.5 2.5 0 1 0 0 5 2.5 2.5 0 0 0 0-5z"/></svg>
        (555) 210-4800
      </li>
      <li class="contact__item">
        <svg class="contact__icon" viewBox="0 0 20 20"><path d="M6 1h8a1 1 0 0 1 1 1v16a1 1 0 0 1-1 1H6a1 1 0 0 1-1-1V2a1 1 0 0 1 1-1zm1 2v11h6V3H7zm3 12.5a1 1 0 1 0 0 2 1 1 0 0 0 0-2z"/></svg>
        (555) 318-7260
      </li>
      <li class="contact__item">
        <svg class="contact__icon" viewBox="0 0 20 20"><path d="M1 4h18v12H1V4zm2 1.5 7 5.5 7-5.5H3zM3 7.5V14h14V7.5l-7 5.5-7-5.5z"/></svg>
        mark@ridgelinetx.com
      </li>
      <li class="contact__item">
        <svg class="contact__icon" viewBox="0 0 20 20"><path d="M10 1a9 9 0 1 0 0 18 9 9 0 0 0 0-18zm-1 3c1 1 0 2-1 3s0 2 1 2 2 1 1 3-1 3-2 4A7 7 0 0 1 4 6c1 0 3 0 5-2zm4 1c1 0 3 2 3 4-1 0-2 1-2 2l-1 3c-1 0-1-2-1-3s-1-2-2-2 0-2 1-2 2-1 2-2z"/></svg>
        www.RidgelineBI.com
      </li>
    </ul>

    <address class="address">4820 Cedar Ridge Drive Suite 110<br>Fairview, TX 75069</address>
  </div>
</body>
</html>
```